Zolvana Stationary and Branding Documents

Corporate Identity Branding stationary needed for IT Recruiting Firm.

I already have a Logo, business cards and website. I need to get designs completed for the remaining corporate identity documents.

The documentation should use similar colors as my website and business card. The designs should modern and clean.

http://zolvanaworks.example/

Target Market(s)

Information Technology Industry

Industry/Entity Type

Information Technology

Colors
3377b5
0255a3
fbee3e
f78f20
f37122
33a6d7
000000
0592cd

Requirements
Must have
• Letter Head
• Folder Design
• PowerPoint Design
• Invoice
• Envelope
Nice to have
• Proposal
• Flyer
• Brochure
Should not have
• Logo
• Business Cards
• Website

```html
<!DOCTYPE html>
<html lang="en">
<head>
<meta charset="utf-8">
<title>Zolvana Folder Design</title>
<link rel="stylesheet" href="https://fonts.googleapis.com/css2?family=Open+Sans:wght@400;600;700&family=Cinzel:wght@500&display=swap">
<style>
:root{
  --stage:#1d74b3;
  --brand-blue:#1f7bc6;
  --deep-blue:#0255a3;
  --navy:#26406e;
  --orange:#f37122;
  --orange-light:#f78f20;
  --white:#ffffff;
  --photo-a:#cfe3ee;
  --photo-b:#7fa7c4;
}
*{box-sizing:border-box;margin:0;padding:0}
html,body{width:1200px;height:847px;overflow:hidden}
body{background:var(--stage);font-family:"Open Sans",Arial,sans-serif;position:relative}
.folder-spread{position:absolute;left:63px;top:43px;width:1074px;height:760px;display:flex;box-shadow:0 16px 40px rgba(0,20,60,.35)}
.panel{position:relative;width:537px;height:760px;background:var(--brand-blue);overflow:hidden}
.panel--back{border-right:1px solid rgba(0,30,80,.35)}
.panel svg.waves{position:absolute;left:0;top:0;width:537px;height:760px}
.photo{background:linear-gradient(135deg,var(--photo-a),var(--photo-b))}
.diamond{position:absolute;width:112px;height:112px;transform:rotate(45deg);border:6px solid var(--white);border-radius:20px;overflow:hidden;box-shadow:0 4px 10px rgba(0,0,0,.3)}
.diamond .photo{width:100%;height:100%}
.diamond--one{left:70px;top:112px}
.diamond--two{left:330px;top:72px}
.diamond--three{left:205px;top:225px}
.brand-name{color:var(--white);font-weight:600;line-height:1}
.back-brand{position:absolute;left:44px;top:560px;font-size:36px}
.contact-list{position:absolute;left:44px;top:612px;color:var(--white);font-size:9px;line-height:15px;list-style:none}
.contact-list svg{width:8px;height:8px;vertical-align:-1px;margin-right:4px;fill:var(--white)}
.back-band{position:absolute;left:0;top:660px;width:537px;height:42px;background:var(--orange);color:var(--white);font-size:8.5px;line-height:13px;text-transform:uppercase;display:flex;align-items:center;justify-content:center;text-align:center;padding:0 24px}
.back-rule,.front-rule{position:absolute;left:0;width:537px;height:3px;background:var(--white)}
.back-rule{top:735px}
.front-photo{position:absolute;left:0;top:0;width:537px;height:340px}
.front-brand{position:absolute;left:0;width:537px;top:470px;text-align:center;font-size:58px}
.front-band{position:absolute;left:0;top:572px;width:537px;height:36px;background:var(--orange);color:var(--white);font-family:"Cinzel",Georgia,serif;font-size:17px;letter-spacing:1px;display:flex;align-items:center;justify-content:center}
.front-rule{top:618px}
.site-pill{position:absolute;left:50%;transform:translateX(-50%);top:650px;background:var(--navy);color:var(--white);font-size:11px;font-weight:700;padding:5px 22px;border-radius:12px 12px 0 0}
</style>
</head>
<body>
<main class="folder-spread">
  <section class="panel panel--back" aria-label="Folder back cover">
    <svg class="waves" viewBox="0 0 537 760" aria-hidden="true">
      <path d="M0 446 Q310 468 537 286" fill="none" stroke="var(--navy)" stroke-width="12"/>
      <path d="M0 432 Q305 454 537 272" fill="none" stroke="var(--orange)" stroke-width="10"/>
      <path d="M0 422 Q300 444 537 262" fill="none" stroke="var(--white)" stroke-width="5"/>
    </svg>
    <div class="diamond diamond--one"><div class="photo" role="img" aria-label="Photo of a smiling professional on the phone in an office"></div></div>
    <div class="diamond diamond--two"><div class="photo" role="img" aria-label="Photo of colleagues in a meeting around a table"></div></div>
    <div class="diamond diamond--three"><div class="photo" role="img" aria-label="Photo of business people shaking hands"></div></div>
    <div class="back-brand brand-name">Zolvana</div>
    <ul class="contact-list">
      <li><svg viewBox="0 0 10 10"><path d="M5 0a3.5 3.5 0 0 0-3.5 3.5C1.5 6 5 10 5 10s3.5-4 3.5-6.5A3.5 3.5 0 0 0 5 0z"/></svg>Two Harbor Plaza 410 Quill Avenue NE &nbsp;☎ 8005550147</li>
      <li><svg viewBox="0 0 10 10"><rect x="0" y="2" width="10" height="6" rx="1"/></svg>info@zolvanaworks.example &nbsp;● zolvanaworks.example</li>
    </ul>
    <p class="back-band">Elite IT talent is no accident. It takes personal drive and smarts, plus smart career counseling. Do you have what it takes? If you do, we provide mentoring and counsel, and we'll stay with you throughout your career.</p>
    <div class="back-rule"></div>
  </section>

  <section class="panel panel--front" aria-label="Folder front cover">
    <div class="front-photo photo" role="img" aria-label="Photo of a business team smiling and working together at a meeting table"></div>
    <svg class="waves" viewBox="0 0 537 760" aria-hidden="true">
      <path d="M0 350 Q240 262 537 268 L537 760 L0 760 Z" fill="var(--white)"/>
      <path d="M0 340 Q240 252 537 258" fill="none" stroke="var(--orange)" stroke-width="9"/>
      <path d="M0 372 Q250 282 537 290 L537 760 L0 760 Z" fill="var(--brand-blue)"/>
    </svg>
    <div class="front-brand brand-name">Zolvana</div>
    <div class="front-band">JOIN THE ELITE</div>
    <div class="front-rule"></div>
    <div class="site-pill">zolvanaworks.example</div>
  </section>
</main>
</body>
</html>
```